Need Primer (paint) Label Design

THE ATTACHED LABEL/S ARE SOLEY FOR REFERENCE. DO NOT MAKE ME AN INTERIOR PAINT OR CHALK PAINT LABEL. I ONLY NEED A "PRIMER" LABEL. THE ATTACHED INTERIOR PAINT LABEL IS ONLY TO SHOW YOU THE THEME/DESIGN OF OUR OTHER LABELS. THE BLUE LABEL ONLY HAS A DESIGN ASPECT I LIKE (PRIMER ON SIDE). The last four labels are our competitors.
```````````````````````````````````````````````````````````````````````````````````````````````````
We need this label to look professional, sharp, eye catching and modern.
OUR PRIMARY COLORS ARE BLACK AND WHITE. IF YOU INCOPORATE ANOTHER COLOR, SILVER OR GOLD MIGHT BE IDEAL BUT PLEASE DON'T DRIFT TOO FAR.
The attached documents:
1st - Our Logo
2nd - Our chalk paint label (reference). We do not need a chalk paint label.
3rd. A random design example. I like the PRIME on the side running vertically. I think it's a cool design concept.
````````````````````````````````````````````````````````````````````````````````````````````````````
We are going to be using a normal paint can with a metal bail/handle so please use that with you design work
``````````````````````````````````````````````````````````````````````````````````````````````````
Order, in my head:
4376
Coatings
^^ I want this to stand out as well but I don't want it to be the first thing your eye is drawn to. Probably 2nd
Interior/Exterior
Multi - Surface Primer
^^ Want this to stick out and draw your eye so the customer knows what it is immediately
Exceptional Adhesion, Performance, Durability,
Use on Wood, Drywall, Plaster, Stucco, Masonry, Brick, Paneling, Painted Metal, & Properly Prepared Glossy Surfaces & More
35* Lowe Temperature Application (can be on side or small)
100% Acrylic
Low Odor - Low VOC - Soap & Water Clean Up
1 US Gallon - 3.785 L
Feel free to get creative with it!

```html
<!DOCTYPE html>
<html lang="en">
<head>
<meta charset="utf-8">
<title>4376 Coatings – Multi Surface Primer Label</title>
<link rel="stylesheet" href="https://fonts.googleapis.com/css2?family=Questrial&family=Montserrat:wght@700;800&family=Barlow:wght@500&display=swap">
<style>
  :root {
    --ink: #000000;
    --paper: #ffffff;
    --silver-light: #ffffff;
    --silver-dark: #8c8c8c;
    --rule: #111111;
  }
  * { margin: 0; padding: 0; box-sizing: border-box; }
  html, body { width: 1200px; height: 927px; overflow: hidden; background: var(--paper); }
  .canvas { position: relative; width: 1200px; height: 927px; }

  .label {
    position: absolute; left: 188px; top: 117px; width: 856px; height: 712px;
    background: var(--ink); box-shadow: 3px 4px 6px rgba(0,0,0,.45);
    color: var(--paper); overflow: hidden;
  }
  .brand-name {
    position: absolute; left: 0; width: 868px; top: 78px; text-align: center;
    font-family: "Questrial", sans-serif; font-weight: 400; color: var(--paper);
  }
  .brand-name .brand-line { display: block; }
  .brand-name .brand-number { font-size: 92px; line-height: 96px; }
  .brand-name .brand-word { font-size: 30px; line-height: 34px; }

  .usage {
    position: absolute; left: 0; width: 868px; top: 254px; text-align: center;
    font-family: "Questrial", sans-serif; font-size: 49px; line-height: 53px;
  }

  .info-band {
    position: absolute; left: 0; top: 407px; width: 774px; height: 241px; color: var(--ink);
    background: linear-gradient(90deg, var(--paper) 0%, var(--paper) 70%, var(--silver-light) 72%, var(--silver-dark) 100%);
  }
  .feature { position: absolute; width: 140px; text-align: center; font-family: "Barlow", sans-serif;
    font-weight: 500; font-size: 11px; line-height: 13px; }
  .feature svg { display: block; margin: 0 auto 3px; }
  .feature-odor { left: 25px; top: 38px; }
  .feature-voc { left: 176px; top: 38px; }
  .feature-clean { left: 23px; top: 131px; }
  .feature-temp { left: 176px; top: 140px; font-size: 10px; line-height: 12px; }
  .temp-value { display: block; font-family: "Montserrat", sans-serif; font-weight: 700;
    font-size: 22px; line-height: 22px; margin-bottom: 4px; padding-left: 24px; }

  .divider { position: absolute; top: 19px; width: 1.5px; height: 186px; background: var(--rule); }
  .divider-a { left: 309px; }
  .divider-b { left: 554px; }

  .benefits { position: absolute; left: 310px; width: 244px; top: 54px; text-align: center;
    font-family: "Barlow", sans-serif; font-weight: 500; font-size: 20px; line-height: 26px; }
  .resin { position: absolute; left: 310px; width: 244px; top: 170px; text-align: center;
    font-family: "Questrial", sans-serif; font-size: 23px; line-height: 23px; }

  .surfaces { position: absolute; left: 560px; width: 230px; top: 48px; text-align: center;
    font-family: "Barlow", sans-serif; font-weight: 500; font-size: 9.5px; line-height: 22.7px; }
  .volume { position: absolute; left: 560px; width: 230px; top: 178px; text-align: center;
    font-family: "Questrial", sans-serif; font-size: 18px; line-height: 20px; letter-spacing: 0.06em; }

  .product-name { position: absolute; left: 0; top: 0; }
  .product-name text { fill: var(--paper); }
  .name-main { font-family: "Montserrat", sans-serif; font-weight: 800; font-size: 112px; }
  .name-sub { font-family: "Montserrat", sans-serif; font-weight: 700; font-size: 52px; }
</style>
</head>
<body>
<div class="canvas">
  <section class="label">
    <div class="brand-name">
      <span class="brand-line brand-number">4376</span>
      <span class="brand-line brand-word">COATINGS</span>
    </div>

    <div class="usage">INTERIOR<br>EXTERIOR</div>

    <div class="info-band">
      <div class="feature feature-odor">
        <svg width="36" height="46" viewBox="0 0 36 46" fill="none" stroke="#000" stroke-width="1.6" stroke-linecap="round">
          <path d="M12 2 C14 10 28 18 30 30 C31 36 26 40 20 39 C17 43 10 42 9 38 C5 38 4 33 7 31"/>
          <path d="M14 33 C17 33 19 35 19 38"/>
          <path d="M17 24 L24 31 M24 24 L17 31"/>
        </svg>
        Low Odor
      </div>
      <div class="feature feature-voc">
        <svg width="50" height="44" viewBox="0 0 50 44" fill="none" stroke="#000" stroke-width="2.4" stroke-linecap="round">
          <path d="M14 8 C20 16 8 24 14 40"/>
          <path d="M22 4 C28 14 16 22 22 40"/>
          <path d="M30 4 C36 14 24 22 30 40"/>
          <path d="M38 8 C44 16 32 24 38 38"/>
          <path d="M3 6 L47 36" stroke-width="1.8"/>
        </svg>
        Low VOC
      </div>
      <div class="feature feature-clean">
        <svg width="26" height="38" viewBox="0 0 26 38" fill="none" stroke="#000" stroke-width="1.6">
          <circle cx="10" cy="4" r="3.2"/>
          <circle cx="7" cy="12" r="3.6"/>
          <circle cx="15" cy="10" r="3.2"/>
          <path d="M13 18 C13 22 20 27 20 31 A7 7 0 0 1 6 31 C6 27 13 22 13 18 Z"/>
        </svg>
        Soap &amp; Water<br>Clean Up
      </div>
      <div class="feature feature-temp">
        <span class="temp-value">35*</span>
        Lowe Temperature<br>Application
      </div>

      <div class="divider divider-a"></div>
      <div class="benefits">Exceptional Adhesion<br>Performance<br>Durability</div>
      <div class="resin">100%<br>ACRYLIC</div>

      <div class="divider divider-b"></div>
      <div class="surfaces">Use on Wood, Drywall, Plaster,<br>Stucco, Masonry, Brick, Paneling,<br>Painted Metal, &amp; Properly Prepared<br>Glossy Surfaces &amp; More</div>
      <div class="volume">1 US GALLON<br>3.785 L</div>
    </div>

    <svg class="product-name" width="856" height="712" viewBox="0 0 856 712">
      <text class="name-main" x="0" y="0" transform="translate(774 397) rotate(-90)" textLength="343" lengthAdjust="spacingAndGlyphs">MULTI</text>
      <text class="name-sub" x="0" y="0" transform="translate(834 648) rotate(-90)" textLength="599" lengthAdjust="spacing">SURFACE PRIMER</text>
    </svg>
  </section>
</div>
</body>
</html>
```